Moravel Aesthetic Doctor

I require an elegant, luxurious looking business card for my aesthetic business. I am a doctor and that will set me aside from competitors. I am planning to provide home and spa based treatments to clients with high expectations. I have attached my logo.

```html
<!DOCTYPE html>
<html lang="en">
<head>
<meta charset="utf-8">
<title>Moravel Aesthetic Doctor – Business Card</title>
<link rel="stylesheet" href="https://fonts.googleapis.com/css2?family=Roboto:ital,wght@0,300;0,400;1,400&display=swap">
<style>
  :root {
    --backdrop: #b9b9b9;
    --card: #f3f3f4;
    --card-edge: #e4e5e7;
    --ink: #2b2d31;
    --brand-grey: #8b93a4;
    --sky: #4fa8db;
    --band-deep: #1c6cb0;
    --band-light: #4d9fd6;
    --swoosh-grey: #8e97a8;
    --white: #ffffff;
  }
  * { box-sizing: border-box; margin: 0; padding: 0; }
  html, body { width: 1200px; height: 576px; overflow: hidden; }
  body {
    background: var(--backdrop);
    font-family: "Roboto", Arial, sans-serif;
    color: var(--ink);
    position: relative;
  }
  .card {
    position: absolute;
    width: 484px;
    height: 292px;
    border-radius: 12px;
    background: linear-gradient(180deg, var(--white) 0%, var(--card) 100%);
    overflow: hidden;
    box-shadow: 0 3px 6px rgba(0,0,0,0.25);
  }
  .card-front { left: 81px; top: 139px; }
  .card-back { left: 602px; top: 139px; }

  /* brand lockup */
  .brand { position: absolute; display: flex; align-items: center; }
  .brand-ring {
    border: 2px solid var(--brand-grey);
    border-radius: 50%;
    flex: none;
  }
  .brand-name {
    font-weight: 300;
    color: var(--brand-grey);
    line-height: 1;
    text-transform: uppercase;
  }
  .brand-name .word { display: block; }
  .card-front .brand { left: 96px; top: 60px; }
  .card-front .brand-ring { width: 90px; height: 90px; margin-right: 18px; }
  .card-front .brand-name .word-main { font-size: 40px; letter-spacing: 2px; }
  .card-front .brand-name .word-sub { font-size: 18px; letter-spacing: 2.4px; margin-top: 6px; }

  .services {
    position: absolute;
    left: 0; right: 0; top: 194px;
    text-align: center;
    font-size: 13px;
    line-height: 19px;
  }
  .services .sep { color: var(--sky); margin: 0 7px; }
  .front-band {
    position: absolute;
    left: 0; right: 0; top: 240px; height: 33px;
    background: linear-gradient(90deg, var(--band-deep) 0%, var(--band-light) 50%, var(--band-deep) 100%);
    color: var(--white);
    font-size: 12.5px;
    letter-spacing: 1px;
    text-align: center;
    line-height: 33px;
  }

  /* back */
  .back-waves { position: absolute; left: 0; top: 0; width: 484px; height: 110px; }
  .back-tagline {
    position: absolute; left: 26px; top: 22px;
    color: var(--white); font-size: 12.5px; line-height: 17px; font-weight: 300;
  }
  .card-back .brand { left: 178px; top: 88px; }
  .card-back .brand-ring { width: 80px; height: 80px; margin-right: 16px; }
  .card-back .brand-name .word-main { font-size: 35px; letter-spacing: 1.6px; }
  .card-back .brand-name .word-sub { font-size: 15.5px; letter-spacing: 2px; margin-top: 5px; }

  .follow {
    position: absolute; left: 26px; top: 179px;
    font-size: 12px; display: flex; align-items: center; gap: 4px;
  }
  .follow .dot { width: 12px; height: 12px; border-radius: 50%; background: var(--sky); display: inline-block; }
  .follow .label { margin-right: 4px; }
  .contacts { position: absolute; left: 26px; top: 207px; list-style: none; font-size: 12.5px; }
  .contacts li { display: flex; align-items: center; height: 18.5px; }
  .contacts svg { width: 11px; height: 11px; margin-right: 11px; fill: var(--sky); }

  .doctor { position: absolute; right: 30px; top: 187px; text-align: right; }
  .doctor-name { font-size: 19px; font-weight: 300; line-height: 22px; }
  .doctor-post { font-size: 10px; font-style: italic; color: var(--sky); margin-top: 2px; }
  .doctor-diploma { font-size: 12.5px; color: var(--sky); line-height: 16px; margin-top: 8px; }
</style>
</head>
<body>

<section class="card card-front" aria-label="Card front">
  <div class="brand">
    <span class="brand-ring"></span>
    <span class="brand-name"><span class="word word-main">Moravel</span><span class="word word-sub">Aesthetic Doctor</span></span>
  </div>
  <p class="services">
    Dermal Injectables<span class="sep">|</span>Plasma Facials<span class="sep">|</span>Microneedling<br>
    Skin Boosters<span class="sep">|</span>Excessive Sweating
  </p>
  <div class="front-band">HOME AND SPA BASED TREATMENTS</div>
</section>

<section class="card card-back" aria-label="Card back">
  <svg class="back-waves" viewBox="0 0 484 110" preserveAspectRatio="none" aria-hidden="true">
    <path d="M0 0 H484 V34 C420 12 330 18 250 48 C170 78 80 88 0 74 Z" fill="var(--sky)"/>
    <path d="M0 74 C80 88 170 78 250 48 C330 18 420 12 484 34 L484 40 C420 22 330 30 255 58 C170 90 80 98 0 90 Z" fill="var(--swoosh-grey)"/>
    <path d="M270 36 C340 8 420 6 484 24 L484 27 C420 11 345 14 275 40 Z" fill="var(--swoosh-grey)" opacity="0.9"/>
  </svg>
  <p class="back-tagline">Home and Spa<br>Based Treatments</p>

  <div class="brand">
    <span class="brand-ring"></span>
    <span class="brand-name"><span class="word word-main">Moravel</span><span class="word word-sub">Aesthetic Doctor</span></span>
  </div>

  <div class="follow"><span class="label">Follow us on:</span><span class="dot"></span><span class="dot"></span></div>
  <ul class="contacts">
    <li><svg viewBox="0 0 12 12"><path d="M2.3 0.6 L4.2 2.9 L3.1 4.2 C3.8 5.9 5.9 8 7.7 8.8 L9 7.7 L11.4 9.6 L10.4 11.3 C6 11.5 0.5 6 0.6 1.6 Z"/></svg>0800 555 014</li>
    <li><svg viewBox="0 0 12 12"><path d="M0.5 2.2 H11.5 V9.8 H0.5 Z M1.2 2.9 L6 6.6 L10.8 2.9 Z" fill-rule="evenodd"/></svg>lena@moravel.co.nz</li>
    <li><svg viewBox="0 0 12 12"><path d="M6 0.5 A5.5 5.5 0 1 0 6 11.5 A5.5 5.5 0 1 0 6 0.5 Z M6 1.5 C7 2.5 7.5 4 7.6 5.5 H4.4 C4.5 4 5 2.5 6 1.5 Z M1.6 6.5 H3.4 C3.5 8 3.9 9.3 4.6 10.3 C3 9.8 1.8 8.3 1.6 6.5 Z M4.4 6.5 H7.6 C7.5 8 7 9.5 6 10.5 C5 9.5 4.5 8 4.4 6.5 Z M8.6 6.5 H10.4 C10.2 8.3 9 9.8 7.4 10.3 C8.1 9.3 8.5 8 8.6 6.5 Z M1.6 5.5 C1.8 3.7 3 2.2 4.6 1.7 C3.9 2.7 3.5 4 3.4 5.5 Z M8.6 5.5 C8.5 4 8.1 2.7 7.4 1.7 C9 2.2 10.2 3.7 10.4 5.5 Z" fill-rule="evenodd"/></svg>www.moravel.co.nz</li>
  </ul>

  <div class="doctor">
    <p class="doctor-name">Dr Lena Vorst</p>
    <p class="doctor-post">MRCPCH MD</p>
    <p class="doctor-diploma">Australasian Diploma of<br>Aesthetic Medicine</p>
  </div>
</section>

</body>
</html>
```